Lumavento business card

We need a modern business card - With our 4 colors - See web: www.lumavento.dk

I have attached logo and som old business Cards we have - Lets Make the new ones shine...:-) -

Industry/Entity Type

Business

Requirements
Must have
• the logo with lumavento only,

```html
<!DOCTYPE html>
<html lang="da">
<head>
<meta charset="utf-8">
<title>Lumavento – visitkort</title>
<link href="https://fonts.googleapis.com/css2?family=Open+Sans:wght@400;600;700&display=swap" rel="stylesheet">
<style>
  :root {
    --lime: #8cc63f;
    --purple: #7b2a8b;
    --magenta: #d6338a;
    --gold: #c9a24a;
    --text-grey: #6b6b6b;
    --ink: #2f2f2f;
    --paper: #ffffff;
    --backdrop: #e6e6e6;
  }
  * { box-sizing: border-box; margin: 0; padding: 0; }
  html, body {
    width: 1200px; height: 950px; overflow: hidden;
    background: var(--backdrop);
    font-family: "Open Sans", Arial, sans-serif;
  }
  .sheet {
    position: relative; width: 1200px; height: 950px;
    display: flex; flex-direction: column; align-items: center;
    justify-content: center; gap: 50px;
  }
  .card {
    position: relative; width: 700px; height: 400px;
    background: var(--paper);
    box-shadow: 0 6px 18px rgba(0,0,0,.18);
    overflow: hidden;
  }
  /* front */
  .card--front { display: flex; align-items: center; justify-content: center; }
  .wordmark {
    display: flex; align-items: center; gap: 14px;
    font-size: 40px; font-weight: 400; letter-spacing: 3px; color: var(--lime);
  }
  .wordmark__dot {
    width: 34px; height: 34px; border-radius: 50%; background: var(--lime);
  }
  /* back */
  .brand-block {
    position: absolute; top: 40px; right: 56px; width: 200px;
    text-align: center;
  }
  .brand-block .wordmark {
    justify-content: center; font-size: 26px; letter-spacing: 2px; gap: 10px;
  }
  .brand-block .wordmark__dot { width: 22px; height: 22px; }
  .brand-block__rule {
    height: 2px; background: var(--lime); margin: 12px 0 8px;
  }
  .brand-block__tagline { font-size: 13px; color: var(--text-grey); }

  .contact {
    position: absolute; left: 48px; top: 118px; color: var(--text-grey);
  }
  .contact__name { font-size: 24px; font-weight: 600; line-height: 1.3; color: var(--lime); }
  .contact__title { font-size: 16px; line-height: 1.4; color: var(--ink); margin-bottom: 14px; }
  .contact__address { font-size: 15px; line-height: 1.3; margin-bottom: 10px; }
  .contact__list { list-style: none; font-size: 15px; line-height: 1.5; }
  .contact__list li { display: flex; align-items: center; gap: 12px; }
  .contact__list svg { width: 15px; height: 15px; fill: var(--lime); flex: none; }

  .band { position: absolute; left: 0; bottom: 0; width: 700px; height: 150px; }
  .band__url {
    position: absolute; left: 48px; bottom: 8px;
    font-size: 18px; font-weight: 700; line-height: 24px;
    color: var(--paper); letter-spacing: .5px;
  }
</style>
</head>
<body>
<main class="sheet">

  <section class="card card--front" aria-label="Visitkort forside">
    <div class="wordmark"><span class="wordmark__dot"></span><span>lumavento</span></div>
  </section>

  <section class="card card--back" aria-label="Visitkort bagside">
    <div class="brand-block">
      <div class="wordmark"><span class="wordmark__dot"></span><span>lumavento</span></div>
      <div class="brand-block__rule"></div>
      <p class="brand-block__tagline">medier til unge</p>
    </div>

    <svg class="band" viewBox="0 0 700 150" aria-hidden="true">
      <defs>
        <linearGradient id="bandStrip" x1="0" x2="1">
          <stop offset="0" stop-color="#7b2a8b"/>
          <stop offset=".4" stop-color="#d6338a"/>
          <stop offset=".7" stop-color="#e86aa0"/>
          <stop offset=".85" stop-color="#8cc63f"/>
          <stop offset="1" stop-color="#c9a24a"/>
        </linearGradient>
        <linearGradient id="bandWedge" x1="0" x2="1">
          <stop offset="0" stop-color="#ffffff" stop-opacity="0"/>
          <stop offset=".35" stop-color="#e86aa0" stop-opacity=".7"/>
          <stop offset=".7" stop-color="#8cc63f"/>
          <stop offset="1" stop-color="#c9a24a"/>
        </linearGradient>
      </defs>
      <polygon points="280,110 700,0 700,110" fill="url(#bandWedge)"/>
      <rect x="0" y="110" width="700" height="40" fill="url(#bandStrip)"/>
    </svg>

    <div class="contact">
      <h1 class="contact__name">Maren Holstvig</h1>
      <p class="contact__title">Salgsdirektør</p>
      <p class="contact__address">Strandlinje Allé 14<br>2000 Frederiksberg<br>Tlf. +45 31 47 62 08</p>
      <ul class="contact__list">
        <li><svg viewBox="0 0 16 16"><path d="M3 2h3l1 3-2 1.5a8 8 0 0 0 4.5 4.5L11 9l3 1v3a1 1 0 0 1-1 1A12 12 0 0 1 2 3a1 1 0 0 1 1-1z"/></svg>+45 31 47 62 08</li>
        <li><svg viewBox="0 0 16 16"><path d="M3 2h3l1 3-2 1.5a8 8 0 0 0 4.5 4.5L11 9l3 1v3a1 1 0 0 1-1 1A12 12 0 0 1 2 3a1 1 0 0 1 1-1z"/></svg>+45 52 19 83 46</li>
        <li><svg viewBox="0 0 16 16"><path d="M1 4h14v9H1z M1 4l7 5 7-5" stroke="#fff" stroke-width="1"/></svg>mh@lumavento.dk</li>
      </ul>
    </div>

    <p class="band__url">www.lumavento.dk</p>
  </section>

</main>
</body>
</html>
```